Design the Business card for NetVaultic

Business card required for a professional Cyber Security business.
Company Logo and Icon has already been provided however I would like other options for the logo and icon to compare to. Alternatively, please refine/enhance the image of the logo.icon I have already provided.

If you are going to use the provided logo and icon, I was thinking that the company raised Logo on White background would serve well on the front of the card. See attached. AND, a large company raised stand-alone icon to appear on black background on the back of the card with tagline 'Cyber Risk Management, Governance and Consulting' or 'Cyber Security for your Business' See attached.
Alternatively, provide your own design for the logo and icon.

Target Market(s)

Enterprise, Government, Financial.

Contact Information for Business Card

Tavin Orloweth
Founder and CEO

Email Address
Mobile Number
Website URL
LinkedIn URL

Logo Text

NetVaultic - see attached example of logo

Font styles to use
Other font styles liked:
• Berlin Sans FB

Requirements
Must have
• Clean large and bold icon on the back with tagline.
• Horizontal alignment,
Nice to have
• Round edges.
• Raised Logo/Icon
Should not have
• An unprofessional look and feel.

```html
<!DOCTYPE html>
<html lang="en">
<head>
<meta charset="utf-8">
<title>NetVaultic Business Card</title>
<link rel="stylesheet" href="https://fonts.googleapis.com/css2?family=Fredoka:wght@500&family=Roboto:wght@400&family=Roboto+Condensed:wght@500&display=swap">
<style>
  :root {
    --page: #e9e7e3;
    --paper: #fbfbfb;
    --ink-dark: #1b1b1c;
    --brand-blue: #1f6fc1;
    --tag-blue: #4d79c9;
    --accent-yellow: #f4b21a;
    --text-grey: #555a60;
    --rule-grey: #9a9a9a;
    --mark-blue: #4872c4;
  }
  * { margin: 0; padding: 0; box-sizing: border-box; }
  html, body { width: 1200px; height: 960px; overflow: hidden; background: var(--page); }
  .canvas { position: relative; width: 1200px; height: 960px; }

  .card { position: absolute; width: 600px; height: 343px; }
  .card-front { left: 314px; top: 113px; background: var(--paper); box-shadow: 0 2px 6px rgba(0,0,0,.18); }
  .card-back { left: 311px; top: 472px; background: var(--ink-dark); box-shadow: 0 2px 6px rgba(0,0,0,.25); }

  .brand-name { font-family: "Fredoka", sans-serif; font-weight: 500; color: var(--brand-blue); white-space: nowrap; }

  .front-logo { position: absolute; left: 36px; top: 40px; display: flex; align-items: center; gap: 12px; }
  .front-logo .brand-dot { width: 60px; height: 60px; border-radius: 50%; background: var(--brand-blue); }
  .front-logo .brand-name { font-size: 40px; }

  .holder { position: absolute; right: 36px; top: 170px; text-align: right; }
  .holder-name { font-family: "Roboto Condensed", sans-serif; font-weight: 500; font-size: 21px; color: var(--brand-blue); letter-spacing: .3px; }
  .holder-title { font-family: "Roboto Condensed", sans-serif; font-weight: 500; font-size: 15px; color: var(--accent-yellow); letter-spacing: .4px; margin-top: 2px; }
  .edge-marker { position: absolute; right: 0; top: 176px; }

  .divider { position: absolute; left: 40px; right: 36px; top: 218px; height: 1.5px; background: var(--rule-grey); }

  .contacts { position: absolute; left: 36px; top: 233px; list-style: none; }
  .contacts li { display: flex; align-items: center; gap: 9px; height: 19px; font-family: "Roboto", sans-serif; font-size: 14px; color: var(--text-grey); }
  .contacts svg { width: 14px; height: 14px; flex: none; }

  .back-mark { position: absolute; left: 17px; top: 17px; width: 300px; height: 306px; border-radius: 50%; background: radial-gradient(circle, #3e63ad 0%, #2a4479 70%, #1b1b1c 100%); }
  .back-brand { position: absolute; left: 345px; top: 226px; }
  .back-brand .brand-name { font-size: 41px; line-height: 1; }
  .tagline { font-family: "Fredoka", sans-serif; font-weight: 500; font-size: 17px; line-height: 19px; margin-top: 6px; }
  .tagline .line-blue { color: var(--tag-blue); display: block; }
  .tagline .line-yellow { color: var(--accent-yellow); display: block; }
</style>
</head>
<body>
<main class="canvas">
  <section class="card card-front">
    <div class="front-logo">
      <span class="brand-dot"></span>
      <span class="brand-name">NetVaultic</span>
    </div>
    <div class="holder">
      <p class="holder-name">TAVIN ORLOWETH</p>
      <p class="holder-title">FOUNDER &amp; CEO</p>
    </div>
    <svg class="edge-marker" width="24" height="32" viewBox="0 0 24 32"><polygon points="24,0 24,32 0,16" fill="var(--brand-blue)"/></svg>
    <div class="divider"></div>
    <ul class="contacts">
      <li><svg viewBox="0 0 14 14"><rect x="3.5" y="0.5" width="7" height="13" rx="1.5" fill="var(--brand-blue)"/><rect x="5" y="2.5" width="4" height="8" fill="#fff"/></svg>555 014 2938</li>
      <li><svg viewBox="0 0 14 14"><rect x="0.5" y="3" width="13" height="9" rx="1" fill="var(--brand-blue)"/><polyline points="1,3.5 7,8 13,3.5" fill="none" stroke="#fff" stroke-width="1.2"/></svg>tavin@netvaultic.com</li>
      <li><svg viewBox="0 0 14 14"><circle cx="7" cy="7" r="6.3" fill="var(--brand-blue)"/><ellipse cx="7" cy="7" rx="2.6" ry="6" fill="none" stroke="#fff" stroke-width="1"/><line x1="1" y1="7" x2="13" y2="7" stroke="#fff" stroke-width="1"/></svg>www.netvaultic.com</li>
      <li><svg viewBox="0 0 14 14"><circle cx="7" cy="7" r="6.3" fill="var(--brand-blue)"/></svg>netvaultic</li>
    </ul>
  </section>

  <section class="card card-back">
    <div class="back-mark" role="img" aria-label="Large company icon area"></div>
    <div class="back-brand">
      <p class="brand-name">NetVaultic</p>
      <p class="tagline">
        <span class="line-blue">Cyber Risk Management</span>
        <span class="line-yellow">Governance &amp; Consulting</span>
      </p>
    </div>
  </section>
</main>
</body>
</html>
```